Verodex business card

Business card for sustainable investment company called "Verodex". Verodex is an exchange platform selling carbon credits between buyers and sellers. Carbon Credits are an environmental commodity for reducing global carbon emissions.

the card should obviously have our logo and the theme should be sustainability/environment mixed with a trading platform.

Contact Information for Business Card

Logo, Name, Title, Phone, Email

Colors
0054AA
0677BA
7BADD7
CADEEF
E8F1F8
0094D4
00A9DD
6FCCEA
C7EBF8
E9F6FB
00AB8E
00BBA5
67D7C9
C6EFE9
E9F9F6
59FF00
82FF00
B8FF75
E3FFCB
F4FFEA

```html
<!DOCTYPE html>
<html lang="en">
<head>
<meta charset="utf-8">
<title>Verodex business card</title>
<link rel="stylesheet" href="https://fonts.googleapis.com/css2?family=Lato:wght@300;400&family=Montserrat:wght@700&display=swap">
<style>
  :root {
    --page: #e4e6e8;
    --card: #161616;
    --white: #ffffff;
    --muted: #e6e6e6;
    --cyan: #4fc6e0;
    --sky: #3ec8f0;
    --blue: #4a86c8;
    --teal: #5fcfe2;
  }
  * { margin: 0; padding: 0; box-sizing: border-box; }
  html, body { width: 1200px; height: 856px; overflow: hidden; }
  body {
    background: var(--page);
    display: flex;
    align-items: center;
    justify-content: center;
    gap: 40px;
    font-family: "Lato", Arial, sans-serif;
  }
  .card {
    position: relative;
    width: 540px;
    height: 309px;
    background: var(--card);
    overflow: hidden;
    box-shadow: 0 6px 18px rgba(0,0,0,0.18);
  }
  .brand {
    display: flex;
    align-items: center;
    gap: 12px;
  }
  .brand-square {
    width: 24px;
    height: 24px;
    background: linear-gradient(135deg, var(--sky), var(--blue));
  }
  .brand-name {
    font-family: "Montserrat", Arial, sans-serif;
    font-weight: 700;
    color: var(--white);
    text-transform: uppercase;
    letter-spacing: 0.5px;
  }
  .front .brand { position: absolute; left: 30px; top: 30px; }
  .front .brand-name { font-size: 30px; }

  .contact-list {
    position: absolute;
    left: 32px;
    top: 96px;
    list-style: none;
    color: var(--muted);
    font-weight: 300;
    font-size: 14px;
    line-height: 24px;
  }
  .contact-list li { display: flex; align-items: center; gap: 9px; }
  .contact-list svg { width: 12px; height: 12px; fill: var(--cyan); }

  .address {
    position: absolute;
    left: 32px;
    top: 196px;
    color: var(--muted);
    font-weight: 300;
    font-size: 15px;
    line-height: 22px;
    font-style: normal;
  }

  .person {
    position: absolute;
    right: 40px;
    top: 32px;
    text-align: right;
  }
  .person-name {
    font-family: "Montserrat", Arial, sans-serif;
    font-weight: 700;
    font-size: 20px;
    color: var(--cyan);
    text-transform: uppercase;
  }
  .person-title {
    font-weight: 300;
    font-size: 15px;
    color: var(--muted);
    margin-top: 2px;
  }
  .accent-bar {
    position: absolute;
    right: 0;
    top: 36px;
    width: 14px;
    height: 40px;
    background: var(--teal);
  }
  .brand-panel {
    position: absolute;
    right: -30px;
    bottom: -70px;
    width: 250px;
    height: 250px;
    border-radius: 14px;
    background: linear-gradient(160deg, var(--teal), var(--sky) 45%, var(--blue));
  }

  .back {
    display: flex;
    align-items: center;
    justify-content: center;
  }
  .back .brand { gap: 18px; }
  .back .brand-square { width: 40px; height: 40px; }
  .back .brand-name { font-size: 52px; }
</style>
</head>
<body>

  <section class="card front">
    <div class="brand">
      <span class="brand-square"></span>
      <span class="brand-name">Verodex</span>
    </div>

    <ul class="contact-list">
      <li>
        <svg viewBox="0 0 24 24"><path d="M6.6 10.8a15.1 15.1 0 0 0 6.6 6.6l2.2-2.2c.3-.3.7-.4 1-.2 1.1.4 2.3.6 3.6.6.6 0 1 .4 1 1V20c0 .6-.4 1-1 1A17 17 0 0 1 3 4c0-.6.4-1 1-1h3.5c.6 0 1 .4 1 1 0 1.3.2 2.5.6 3.6.1.3 0 .7-.2 1z"/></svg>
        123 456 789
      </li>
      <li>
        <svg viewBox="0 0 24 24"><path d="M2 5h20v14H2z M2 5l10 8 10-8" fill="none" stroke="currentColor"/><path d="M2 5h20v2l-10 7L2 7zM2 9l10 7 10-7v10H2z"/></svg>
        hello@verodex.com
      </li>
      <li>
        <svg viewBox="0 0 24 24"><path d="M12 2a10 10 0 1 0 0 20 10 10 0 0 0 0-20zm0 2c1.2 1.3 2 3.4 2.2 7H9.8c.2-3.6 1-5.7 2.2-7zm-3.9.9C7.4 6.6 7 8.6 6.8 11H4.1a8 8 0 0 1 4-6.1zm7.8 0a8 8 0 0 1 4 6.1h-2.7c-.2-2.4-.6-4.4-1.3-6.1zM4.1 13h2.7c.2 2.4.6 4.4 1.3 6.1a8 8 0 0 1-4-6.1zm5.7 0h4.4c-.2 3.6-1 5.7-2.2 7-1.2-1.3-2-3.4-2.2-7zm7.4 0h2.7a8 8 0 0 1-4 6.1c.7-1.7 1.1-3.7 1.3-6.1z"/></svg>
        www.verodex.com
      </li>
    </ul>

    <address class="address">
      Your address, City<br>
      State, Zip 1234
    </address>

    <div class="person">
      <p class="person-name">Daniel Reeve</p>
      <p class="person-title">Managing Director</p>
    </div>
    <span class="accent-bar"></span>

    <div class="brand-panel" role="img" aria-label="Large brand symbol decoration"></div>
  </section>

  <section class="card back">
    <div class="brand">
      <span class="brand-square"></span>
      <span class="brand-name">Verodex</span>
    </div>
  </section>

</body>
</html>
```